Maplecrest Cove Retreat Wedding and Event Venue

We are looking for a webpage for our Wedding and Event Venue just opened up in Eastern San Diego CA. It is out of a private home that has a very photogenic backyard including grapevines and orchard trees, a 15 ft waterfall into a pool and market lights hanging from trees, all connected by paved stone and compacted dirt paths

We are looking for something that will be very bright, warm and inviting to our clients. The clientele will be mostly couples between 22 and 35 years of age for the weddings and planners/executives age 22-60 for our corporate events.

We would like a rustic Outdoor look as that is what our venue showcases. You can see our facebook Here: https://www.facebook.com/MaplecrestCoveRetreat/

We would like for the pictures on the facebook to be used on the page. The google drive where most of them are located is here for full file sizes https://files.examplecloud.net/open?id=7Q-9Kpt-M2xvaT8LwQeRTp4-DN5H

We would like to see designs that go with the colors of our logo and that included stone, wood, and grapevine textures as well as anything else rustic such as Market-lights.

The final design should be welcoming for newly engaged couples and corporations/companies who would like to book an outdoor venue for their wedding or next event. There can even be a simple first page with separate tabs for weddings and events that will be able to be more specially focused to the clients.

We would also like the option to be able to edit the pictures we place on the site seasonally as we would like our pictures to reflect our clients

Target Market(s)

Engaged couples age 22-35 and corporate planners/executives age 22-60

Industry/Entity Type

Events

Font styles to use
Script

Requirements
Must have
• Rustic Look, (wood, stone, wine vines/barrels, market lights, mason jars, etc)
• tab pages/sub pages for "About us", "Packages", "Pricing", "Gallery" (we must be able to put our pictures here from all our events), "What makes us Unique", "Contact us" that we are able to enter information into
Nice to have
• Colors matching our logo, Pictures from our Facebook page (listed in brief)
Should not have
• Corporate Look

```html
<!DOCTYPE html>
<html lang="en">
<head>
<meta charset="utf-8">
<title>Maplecrest Cove Retreat Wedding and Event Venue</title>
<link rel="stylesheet" href="https://fonts.googleapis.com/css2?family=Cinzel:wght@400;600&family=Cormorant+Garamond:ital,wght@0,500;1,500&family=Open+Sans:wght@400;600;700&display=swap">
<style>
:root{
  --gold:#b08d4a;
  --gold-soft:#c7a66a;
  --wood:#e9e3d7;
  --wood-dark:#d9cfbe;
  --ink:#5e5244;
  --ink-soft:#7d7264;
  --white:#ffffff;
  --cream:#f3efd6;
  --sage:#8c9f88;
  --sage-line:#a9b8a6;
}
*{margin:0;padding:0;box-sizing:border-box}
html,body{width:1200px;height:4054px;overflow:hidden}
body{position:relative;font-family:"Open Sans",Arial,sans-serif;color:var(--ink);background:var(--wood)}
.abs{position:absolute}
.photo{position:absolute}
.heading{font-family:"Cinzel",Georgia,serif;letter-spacing:1px;text-transform:uppercase;text-align:center;position:absolute;left:0;width:1200px}
.body-text{font-size:13px;line-height:22px;color:var(--ink-soft)}

/* hero */
.hero{position:absolute;left:0;top:0;width:1200px;height:662px;background:radial-gradient(ellipse at 60% 45%,#6a4e7a 0%,#3a2c3a 35%,#1d1a1f 75%)}
.brand{position:absolute;left:127px;top:38px;width:190px;text-align:center;font-family:"Cinzel",Georgia,serif;font-weight:600;font-size:19px;line-height:25px;color:var(--gold-soft)}
.nav{position:absolute;top:76px;right:105px;display:flex;gap:22px;list-style:none}
.nav a{color:var(--white);text-decoration:none;font-size:13px;font-weight:700;letter-spacing:.3px}
.hero-title{top:268px;font-size:52px;line-height:58px;color:var(--white);font-weight:600}
.hero-sub{position:absolute;top:395px;left:0;width:1200px;text-align:center;font-family:"Cormorant Garamond",Georgia,serif;font-size:32px;color:var(--white)}
.slider-dots{position:absolute;left:1096px;top:262px;display:flex;flex-direction:column;gap:10px}
.slider-dots span{width:9px;height:9px;border-radius:50%;background:rgba(255,255,255,.5)}
.slider-dots span:first-child{background:var(--white)}

/* about */
.about{position:absolute;top:662px;left:0;width:1200px;height:433px;background:linear-gradient(180deg,#efe9de,#e3dccd)}
.about .heading{top:88px;font-size:34px;color:var(--ink)}
.rule{position:absolute;height:1px;background:var(--gold)}
.about p{position:absolute;top:150px;left:265px;width:670px;text-align:center}

/* unique */
.unique{position:absolute;top:1095px;left:0;width:1200px;height:459px;background:radial-gradient(ellipse at 50% 40%,#7a6a55 0%,#3e3428 45%,#1e1a16 90%)}
.unique .heading{top:112px;font-size:44px;color:var(--white)}
.unique p{position:absolute;top:208px;left:340px;width:520px;text-align:center;color:var(--white);font-size:14px;line-height:22px}
.btn{position:absolute;height:44px;border-radius:22px;font-size:13px;font-weight:600;letter-spacing:1px;display:flex;align-items:center;justify-content:center;text-transform:uppercase}
.btn-light{left:530px;top:280px;width:150px;border:2px solid var(--white);color:var(--white)}

/* features */
.features{position:absolute;top:1554px;left:0;width:1200px;height:879px;background:linear-gradient(180deg,#ebe5d9,#ddd5c6)}
.frame{position:absolute;top:103px;width:308px;height:281px;border:4px solid #f5f1ea;box-shadow:0 2px 6px rgba(0,0,0,.15)}
.col{position:absolute;top:455px;width:446px}
.col p{margin-bottom:16px}
.btn-gold{left:505px;top:740px;width:178px;border:2px solid var(--gold);color:var(--gold);font-family:"Cinzel",Georgia,serif}

/* packages */
.packages-band{position:absolute;top:2433px;left:0;width:1200px;height:419px;background:linear-gradient(90deg,#d8b8a2 0%,#efe2d6 45%,#d99b8d 100%)}
.packages-band .heading{top:165px;font-size:44px;color:var(--white)}
.pricing{position:absolute;top:2852px;left:0;width:1200px;height:784px;background:radial-gradient(ellipse at 50% 30%,#f7f3df,#e8e6c4 80%)}
.plan{position:absolute;top:64px;width:240px}
.plan h3{font-family:"Cinzel",Georgia,serif;font-weight:400;font-size:25px;color:var(--gold);line-height:28px}
.plan .price{font-family:"Cormorant Garamond",Georgia,serif;font-weight:500;font-size:30px;color:var(--ink);line-height:36px;margin-bottom:8px}
.pframe{position:absolute;top:424px;height:257px;border:4px solid #f7f4ea;box-shadow:0 2px 6px rgba(0,0,0,.12)}

/* footer */
.footer{position:absolute;top:3636px;left:0;width:1200px;height:418px;background:var(--sage);color:var(--white)}
.social{position:absolute;left:122px;top:45px;display:flex;gap:9px}
.social span{width:20px;height:20px;border-radius:50%;background:var(--white)}
.footer h4{position:absolute;font-size:16px;font-weight:600;letter-spacing:.5px}
.loc{position:absolute;top:158px;font-size:12px;line-height:18px}
.links{position:absolute;left:880px;top:151px;list-style:none;font-size:12px;line-height:22px}
.footer-rule{position:absolute;left:122px;top:336px;width:956px;height:1px;background:var(--sage-line)}
.copy{position:absolute;top:364px;left:0;width:1200px;text-align:center;font-size:12px;color:#e4ebe2}
</style>
</head>
<body>

<header class="hero">
  <div class="photo" role="img" aria-label="Bride and groom dancing with guests under colored evening lights" style="inset:0"></div>
  <div class="brand">Maplecrest Cove Retreat</div>
  <ul class="nav">
    <li><a href="#">HOME</a></li>
    <li><a href="#">ABOUT US</a></li>
    <li><a href="#">PACKAGES</a></li>
    <li><a href="#">PRICING</a></li>
    <li><a href="#">GALLERY</a></li>
    <li><a href="#">WHAT MAKES US UNIQUE</a></li>
    <li><a href="#">CONTACT US</a></li>
  </ul>
  <h1 class="heading hero-title">Private Wedding and<br>Event Venue</h1>
  <p class="hero-sub">Book Your Event with us Now</p>
  <div class="slider-dots"><span></span><span></span><span></span><span></span></div>
  <svg class="abs" style="left:585px;top:604px" width="30" height="18" viewBox="0 0 30 18"><path d="M2 2 L15 15 L28 2" fill="none" stroke="#fff" stroke-width="2.5"/></svg>
</header>

<section class="about">
  <div class="rule" style="left:270px;top:110px;width:216px"></div>
  <h2 class="heading">About Us</h2>
  <div class="rule" style="left:714px;top:110px;width:218px"></div>
  <p class="body-text">Tucked into the hills east of San Diego, our private home opens its backyard to weddings and gatherings. Grapevines, orchard trees and a fifteen foot waterfall set the scene, while market lights glow over stone paths. We keep every day personal, relaxed and full of warmth for you and your guests.</p>
</section>

<section class="unique">
  <h2 class="heading">What Makes Us Unique</h2>
  <p>A private backyard venue with vines, orchard shade and a waterfall pool, lit by strings of market lights after sunset.</p>
  <a class="btn btn-light">Book Now</a>
</section>

<section class="features">
  <div class="frame" role="img" aria-label="Bridesmaids helping the bride get ready" style="left:116px;background:linear-gradient(135deg,#f4ede6,#d9c3b0)"></div>
  <div class="frame" role="img" aria-label="Flower-covered ceremony arch in a green garden" style="left:446px;background:linear-gradient(135deg,#c9d8b8,#7d9a66)"></div>
  <div class="frame" role="img" aria-label="Bride having her makeup done by a window" style="left:776px;background:linear-gradient(135deg,#efe4dc,#cdb39e)"></div>
  <div class="col body-text" style="left:122px">
    <p>Getting ready is part of the day. Our bridal suite has soft window light, wide mirrors and room for the whole party to laugh, pin flowers and take photos before the walk down the aisle.</p>
    <p>Ceremonies happen beneath the garden arch, framed by green leaves and the sound of falling water from the pool.</p>
  </div>
  <div class="col body-text" style="left:635px">
    <p>From the first dance to the last toast, the lawn and stone terrace hold up to one hundred and fifty guests, with tables, chairs and lighting already in place for your evening.</p>
    <p>Corporate teams enjoy the same calm setting for retreats, lunches and award nights away from the office.</p>
  </div>
  <a class="btn btn-gold">View Gallery</a>
</section>

<section class="packages-band" role="img" aria-label="Two bridesmaids in red dresses holding bouquets">
  <h2 class="heading">Packages</h2>
</section>

<section class="pricing">
  <div class="plan" style="left:135px">
    <h3>First Package</h3>
    <div class="price">$125.99</div>
    <p class="body-text">An afternoon in the garden for small ceremonies and elopements. Includes four hours on site, the arch, chairs for forty guests and a quiet spot for photos by the waterfall.</p>
  </div>
  <div class="plan" style="left:460px">
    <h3>Second Package</h3>
    <div class="price">$225.99</div>
    <p class="body-text">Our most loved choice for weddings. Eight hours on site, ceremony and reception areas, market lights, tables and chairs for one hundred guests and use of the bridal suite.</p>
  </div>
  <div class="plan" style="left:792px">
    <h3>Third Package</h3>
    <div class="price">$425.99</div>
    <p class="body-text">The whole property for a full day. Setup the evening before, every space on the grounds, lighting, seating for one hundred fifty and a coordinator to guide your event.</p>
  </div>
  <div class="pframe" role="img" aria-label="Pale blue wedding sneakers beside a veil" style="left:127px;width:460px;background:linear-gradient(135deg,#e8e6e2,#a9bfcf)"></div>
  <div class="pframe" role="img" aria-label="Bridal party in matching robes sitting together" style="left:614px;width:456px;background:linear-gradient(135deg,#e6d2c8,#b88d7e)"></div>
</section>

<footer class="footer">
  <div class="social"><span></span><span></span><span></span><span></span><span></span></div>
  <h4 style="left:122px;top:110px">LOCATIONS</h4>
  <div class="loc" style="left:122px">Alpine<br>1480 Oak Ridge Lane<br>Alpine, CA — 91901<br>(619) 555-0142</div>
  <div class="loc" style="left:346px">Jamul<br>27 Vineyard Road<br>Jamul, CA — 91935<br>(619) 555-0178</div>
  <div class="loc" style="left:611px">Food Truck<br>310 Market Lane<br>El Cajon, CA — 92019<br>(619) 555-0193</div>
  <h4 style="left:870px;top:110px">QUICK LINKS</h4>
  <ul class="links">
    <li>Home</li><li>About us</li><li>Packages</li><li>Pricing</li><li>Gallery</li>
  </ul>
  <div class="footer-rule"></div>
  <p class="copy">© 2017 Company Name. All right reserved. Term of Use</p>
</footer>

</body>
</html>
```